Exciting product design for natural pet treats

We need a design for our stand up doy style pouch that blends well with our current logo and also bold enough to stand out from the crowd.

We have a range of natural, Australian made pet treats and need a generic bag that allows for a sticker to be placed on the bag to idenfity the name, while also allowing a space for another sticker on the back for ingredients.
___
Information for the front is: logo, Australian made and owned, Pet Food Only (this is a small font and should not be hero text), 100% Natural, Visit our web site for more amazing products for your pets, Space for sticker 100 - 150mm x 30mm.
___
Information for the back is: Tailwag Depot is proudly Australian owned and operated. We source all our Tailwag Depot treats from reputable suppliers around Australia.

Our Tailwag Depot treats can be purchased through our online store, where you will find a growing range of other brands and products for your dogs, cats, birds, fish, rabbits, guinea pigs, horses, cows, sheep, chickens and more.

For further information, please visit our web site www.tailwagdepot.com.au or email us directly info@tailwagdepot.com.au.
____
The design will be used on three different bag sizes, so our printer can reduce the design from the largest size, but please keep in mind the sizes are 280mm x 380mm, 190mm x 275mm & 160mm x 230mm.

Target Market(s)

Mostly female, 25 to 65 years of age. Pet Lovers, particuarly focussing on dogs.

Industry/Entity Type

pet industry

Requirements
Must have
• Space for sticker on front for the product name 100mm x 30mm. Also a
Nice to have
• Space for a window.
Should not have
• comical pet images. Does not need an image of a pet. Does not need an image of the food.

```html
<!DOCTYPE html>
<html lang="en">
<head>
<meta charset="utf-8">
<title>Tailwag Depot – Treat Pouch Front and Back</title>
<link rel="stylesheet" href="https://fonts.googleapis.com/css2?family=Oswald:wght@500;600&family=Josefin+Sans:wght@400;600&display=swap">
<style>
  :root {
    --backdrop: #e7e6e3;
    --pouch: #f3f3f5;
    --pouch-edge: #dcdce0;
    --purple: #4d2a86;
    --purple-soft: #7a4fc0;
    --teal: #3aa9b8;
    --teal-dark: #2f8795;
    --ghost: rgba(80, 80, 90, 0.10);
    --window-light: #a88a63;
    --window-dark: #6e5438;
  }
  * { box-sizing: border-box; margin: 0; padding: 0; }
  html, body { width: 1200px; height: 799px; overflow: hidden; }
  body {
    background: var(--backdrop);
    font-family: "Oswald", "Arial Narrow", sans-serif;
    color: var(--purple);
    position: relative;
  }
  .pouch {
    position: absolute;
    top: 60px;
    width: 460px;
    height: 680px;
    background: var(--pouch);
    border: 1px solid var(--pouch-edge);
    border-radius: 6px;
    box-shadow: 0 10px 30px rgba(0,0,0,0.08);
    overflow: hidden;
    text-align: center;
  }
  .pouch--front { left: 110px; }
  .pouch--back { left: 630px; }
  .pouch__seal {
    position: absolute; left: 0; right: 0; top: 0; height: 70px;
    border-bottom: 1px solid var(--pouch-edge);
  }
  .pouch__zip {
    position: absolute; left: 0; right: 0; top: 82px; height: 4px;
    border-top: 1px solid var(--pouch-edge);
    border-bottom: 1px solid var(--pouch-edge);
  }
  .brand {
    position: absolute; left: 0; right: 0;
    display: flex; align-items: center; justify-content: center; gap: 12px;
  }
  .brand__dot {
    width: 40px; height: 40px; border-radius: 50%;
    border: 3px solid var(--teal);
  }
  .brand__name {
    font-family: "Oswald", "Arial Narrow", sans-serif;
    font-weight: 600;
    color: var(--purple);
    letter-spacing: 0.5px;
  }
  .pouch--front .brand { top: 120px; flex-direction: column; gap: 14px; }
  .pouch--front .brand__dot { width: 90px; height: 90px; border-width: 4px; }
  .pouch--front .brand__name { font-size: 46px; line-height: 1; }
  .tagline-small {
    position: absolute; left: 0; right: 0; top: 294px;
    font-family: "Josefin Sans", sans-serif; font-weight: 600;
    font-size: 14px; letter-spacing: 1px; color: var(--purple-soft);
  }
  .sticker-space {
    position: absolute;
    border: 2px dashed var(--purple-soft);
    border-radius: 18px;
  }
  .pouch--front .sticker-space { left: 135px; top: 325px; width: 190px; height: 130px; }
  .silhouette {
    position: absolute; background: var(--ghost); border-radius: 40px;
  }
  .silhouette--cat { left: 30px; top: 330px; width: 75px; height: 210px; }
  .silhouette--dog { right: 28px; top: 310px; width: 70px; height: 190px; }
  .food-window {
    position: absolute; left: 125px; top: 472px; width: 210px; height: 96px;
    border-radius: 40px;
    background: linear-gradient(135deg, var(--window-light), var(--window-dark));
  }
  .visit {
    position: absolute; left: 0; right: 0; top: 586px;
    font-size: 17px; line-height: 1.15; font-weight: 500; text-transform: uppercase;
  }
  .url-pill {
    position: absolute; left: 110px; top: 636px; width: 240px; height: 28px;
    background: var(--teal-dark); color: #fff; border-radius: 14px;
    font-family: "Josefin Sans", sans-serif; font-size: 13px; letter-spacing: 1px;
    line-height: 30px; text-transform: uppercase;
  }
  .natural-badge {
    position: absolute; right: 22px; top: 600px; width: 56px;
    font-family: "Josefin Sans", sans-serif; font-weight: 600; font-size: 10px;
    color: #222; line-height: 1.1;
  }
  .natural-badge svg { display: block; margin: 0 auto 3px; }

  .pouch--back .brand { top: 110px; }
  .pouch--back .brand__name { font-size: 34px; }
  .origin {
    position: absolute; left: 0; right: 0; top: 166px;
    font-family: "Josefin Sans", sans-serif; font-weight: 600;
    font-size: 11px; letter-spacing: 1.5px; color: var(--teal); text-transform: uppercase;
  }
  .sourcing {
    position: absolute; left: 40px; right: 40px; top: 186px;
    font-size: 19px; line-height: 1.2; font-weight: 500; color: var(--purple-soft);
    text-transform: uppercase;
  }
  .ingredients-label {
    position: absolute; left: 0; right: 0; top: 246px;
    font-family: "Josefin Sans", sans-serif; font-size: 10px; letter-spacing: 1px;
    color: var(--teal); text-transform: uppercase;
  }
  .pouch--back .sticker-space { left: 120px; top: 264px; width: 220px; height: 150px; }
  .ghost-mark {
    position: absolute; left: 70px; top: 390px; width: 320px; height: 320px;
    border: 3px solid var(--ghost); border-radius: 50%;
  }
  .store-copy {
    position: absolute; left: 40px; right: 40px; top: 440px;
    font-size: 15px; line-height: 1.3; font-weight: 500; text-transform: uppercase;
  }
  .contact {
    position: absolute; left: 30px; right: 30px; top: 580px;
    font-size: 15px; line-height: 1.35; font-weight: 500; text-transform: uppercase;
  }
  .contact__heading { color: var(--teal-dark); }
</style>
</head>
<body>

<section class="pouch pouch--front" aria-label="Pouch front">
  <div class="pouch__seal"></div>
  <div class="pouch__zip"></div>
  <div class="silhouette silhouette--cat" role="img" aria-label="Faint cat silhouette decoration"></div>
  <div class="silhouette silhouette--dog" role="img" aria-label="Faint dog silhouette decoration"></div>
  <div class="brand">
    <span class="brand__dot"></span>
    <span class="brand__name">Tailwag Depot</span>
  </div>
  <p class="tagline-small">PET FOOD ONLY</p>
  <div class="sticker-space" aria-label="Space for product name sticker"></div>
  <div class="food-window" role="img" aria-label="Window showing the treats inside the pouch"></div>
  <p class="visit">Visit our web site for more<br>amazing products for your pets</p>
  <div class="url-pill">www.tailwagdepot.com.au</div>
  <div class="natural-badge">
    <svg width="22" height="22" viewBox="0 0 22 22" aria-hidden="true"><path d="M4 18 C4 8 10 3 19 3 C19 12 14 18 4 18Z" fill="#222"/></svg>
    100%<br>NATURAL
  </div>
</section>

<section class="pouch pouch--back" aria-label="Pouch back">
  <div class="pouch__seal"></div>
  <div class="pouch__zip"></div>
  <div class="ghost-mark"></div>
  <div class="brand">
    <span class="brand__dot"></span>
    <span class="brand__name">Tailwag Depot</span>
  </div>
  <p class="origin">Proudly Australian owned and operated</p>
  <p class="sourcing">We source all our Tailwag Depot treats from reputable suppliers around Australia.</p>
  <p class="ingredients-label">Ingredients:</p>
  <div class="sticker-space" aria-label="Space for ingredients sticker"></div>
  <p class="store-copy">Our Tailwag Depot treats can be purchased through our online store, where you will find a growing range of other brands and products for your dogs, cats, birds, fish, rabbits, guinea pigs, horses, cows, sheep, chickens and more.</p>
  <p class="contact">
    <span class="contact__heading">For further information:</span><br>
    Please visit our web site www.tailwagdepot.com.au or<br>
    email us directly info@tailwagdepot.com.au
  </p>
</section>

</body>
</html>
```